U.S. Popcorn company needs business cards

We are a popcorn company that manufactures popcorn and sells it to grocery stores worldwide. Our theme is "Americana" and our logo is U.S. route 66 which is the most famous highway in the U.S.

We would like the design to be simple and to use both sides. On the back side we would like to see just the logo and website. The front would be normal details

Target Market(s)

Wholesalers, grocers and distributors

Industry/Entity Type

Manufacture

Contact Information for Business Card

Business name: Prairie Lantern Popcorn
Phone: +1 555 308 4726
Email: Dale@prairielanternpopcorn.com
website: www.prairielanternpopcorn.com
Tag Line: "Fresh from the kettle"
Name: Dale Whitcombe
Title: Founder/President

Requirements
Must have
• Either this design should be fun or clean and simple. I will let you show me your thougths.
Nice to have
• Anything that ties in the real Hwy Route 66.
• Colors might need to be red, white and blue incorporated.
Should not have
• Not be too busy.

```html
<!DOCTYPE html>
<html lang="en">
<head>
<meta charset="utf-8">
<title>Prairie Lantern Popcorn – Business Cards</title>
<link rel="stylesheet" href="https://fonts.googleapis.com/css2?family=Source+Sans+3:ital,wght@0,400;0,600;1,400;1,600&display=swap">
<style>
  :root {
    --navy: #0b2a6b;
    --red: #e31e24;
    --white: #ffffff;
    --ink-grey: #555555;
    --backdrop: #e9e6e1;
  }
  * { margin: 0; padding: 0; box-sizing: border-box; }
  html, body {
    width: 1200px;
    height: 987px;
    overflow: hidden;
  }
  body {
    background: var(--backdrop);
    font-family: "Source Sans 3", "Myriad Pro", Arial, sans-serif;
    position: relative;
  }
  .card {
    position: absolute;
    left: 293px;
    width: 615px;
    height: 351px;
    overflow: hidden;
    box-shadow: 0 2px 5px rgba(0,0,0,0.25);
  }
  /* Front */
  .card-front {
    top: 130px;
    background: var(--white);
  }
  .brand-panel {
    position: absolute;
    left: 0; top: 0;
    width: 250px;
    height: 100%;
    background: var(--navy);
    display: flex;
    align-items: center;
    justify-content: center;
    padding: 0 24px;
  }
  .brand-name {
    color: var(--white);
    font-weight: 600;
    font-size: 34px;
    line-height: 1.1;
    text-align: center;
  }
  .edge-tab {
    position: absolute;
    right: 0;
    top: 203px;
    width: 9px;
    height: 42px;
    background: var(--navy);
  }
  .contact-block {
    position: absolute;
    right: 27px;
    top: 193px;
    text-align: right;
  }
  .person-name {
    color: var(--navy);
    font-weight: 600;
    font-size: 24px;
    line-height: 1.1;
  }
  .person-title {
    color: var(--red);
    font-size: 17px;
    line-height: 1.2;
    margin-bottom: 12px;
  }
  .contact-list { list-style: none; }
  .contact-list li {
    display: flex;
    justify-content: flex-end;
    align-items: center;
    gap: 10px;
    color: var(--ink-grey);
    font-size: 15px;
    line-height: 23px;
  }
  .contact-list svg {
    width: 15px;
    height: 15px;
    flex: none;
  }
  /* Back */
  .card-back {
    top: 506px;
    background: var(--red);
  }
  .back-brand {
    position: absolute;
    left: 0; right: 0;
    top: 100px;
    text-align: center;
    color: var(--white);
    font-weight: 600;
    font-size: 40px;
    line-height: 1.1;
  }
  .tagline {
    position: absolute;
    left: 0; right: 0;
    top: 296px;
    text-align: center;
    color: var(--white);
    font-size: 19px;
    font-style: italic;
    font-weight: 600;
  }
</style>
</head>
<body>
  <section class="card card-front" aria-label="Business card front">
    <div class="brand-panel">
      <p class="brand-name">Prairie Lantern Popcorn</p>
    </div>
    <div class="edge-tab"></div>
    <div class="contact-block">
      <p class="person-name">Dale Whitcombe</p>
      <p class="person-title">Founder/President</p>
      <ul class="contact-list">
        <li>+1 555 308 4726
          <svg viewBox="0 0 16 16" aria-hidden="true"><path fill="var(--navy)" d="M3.2 1.5l2.3-.4 1.4 3.3-1.6 1.2c.8 1.8 2.2 3.2 4 4l1.2-1.6 3.3 1.4-.4 2.3c-.2.8-.9 1.3-1.7 1.3C6.2 13 3 9.8 2 4.9c0-.8.4-1.7 1.2-2.4z"/></svg>
        </li>
        <li>Dale@prairielanternpopcorn.com
          <svg viewBox="0 0 16 16" aria-hidden="true"><rect x="1" y="3" width="14" height="10" fill="var(--navy)"/><path d="M1.5 3.5L8 9l6.5-5.5" fill="none" stroke="var(--white)" stroke-width="1.2"/></svg>
        </li>
        <li>www.prairielanternpopcorn.com
          <svg viewBox="0 0 16 16" aria-hidden="true"><circle cx="8" cy="8" r="7" fill="var(--navy)"/><path d="M5 4.5c1.5.3 2 1.5 1.2 2.5-.8.9.2 2 1.3 2.2.8.2.6 1.8-.2 2.8M10 3.5c-.6 1.2.4 2 1.5 2.3" fill="none" stroke="var(--white)" stroke-width="1.2"/></svg>
        </li>
      </ul>
    </div>
  </section>

  <section class="card card-back" aria-label="Business card back">
    <p class="back-brand">Prairie Lantern<br>Popcorn</p>
    <p class="tagline">Fresh from the kettle</p>
  </section>
</body>
</html>
```